The Aldermoor- outdoor banner

This should be a horizontal banner. It should have the logos attached incorporated and the following details
Coming Spring 2025: The Aldermoor - Exclusive Luxury Condos
Listed by Marisol Quennell | Fairlight Realty
Construction by Stonegate Build Group
Unveil the height of luxury living with The Aldermoor, a new condo building in East Boston, set for completion in Spring 2025. Experience a standard of elegance and sophistication like never before.
For more information and inquiries, please contact:
Marisol Quennell
Phone: (617) 430-9162
Email: marisol@fairlightprops.com
The banner should be very classy incorporting gold and navy very classic fonts. The Aldermoor should look very classy and exclusive. The stonegate build group logo should be smaller. It should not include their phone number and instagram handle only the name of the company. Herringbone pattern in the background would be great. This is going outside the building to advertise pre construction units

```html
<!DOCTYPE html>
<html lang="en">
<head>
<meta charset="utf-8">
<title>The Aldermoor – Outdoor Banner</title>
<link href="https://fonts.googleapis.com/css2?family=Cinzel:wght@400;700;800&family=Great+Vibes&family=Poppins:wght@500;600&display=swap" rel="stylesheet">
<style>
  :root {
    --navy: #12245a;
    --navy-deep: #0c1a44;
    --navy-band: #0b1738;
    --gold: #e8b962;
    --gold-soft: #eabb66;
    --white: #ffffff;
    --panel-light: #f3f3f4;
    --panel-shade: #dcdcde;
    --page: #e6e6e8;
  }
  html, body {
    margin: 0;
    padding: 0;
    width: 1025px;
    height: 1200px;
    overflow: hidden;
    background: var(--page);
  }
  .banner {
    position: absolute;
    left: 20px;
    top: 455px;
    width: 985px;
    height: 290px;
    overflow: hidden;
    box-shadow: 0 10px 24px rgba(0,0,0,0.28);
    background: linear-gradient(90deg, var(--navy-deep) 0%, var(--navy) 100%);
  }
  .banner-shapes {
    position: absolute;
    inset: 0;
  }
  .brand {
    position: absolute;
    left: 20px;
    top: 28px;
    width: 232px;
    text-align: center;
    color: var(--gold);
    font-family: "Cinzel", serif;
    font-weight: 400;
  }
  .brand-mark {
    width: 72px;
    height: 72px;
    margin: 0 auto 8px;
    border: 3px solid var(--gold);
    border-radius: 50%;
    box-sizing: border-box;
  }
  .brand-name {
    font-size: 28px;
    line-height: 1;
    letter-spacing: 1px;
  }
  .brand-sub {
    font-size: 11px;
    letter-spacing: 9px;
    margin-top: 6px;
    padding-left: 9px;
  }
  .launch {
    position: absolute;
    left: 270px;
    top: 18px;
    display: flex;
    align-items: center;
    gap: 14px;
  }
  .launch-script {
    font-family: "Great Vibes", cursive;
    color: var(--white);
    font-size: 40px;
    line-height: 1;
  }
  .launch-year {
    background: var(--gold);
    color: var(--navy-deep);
    font-family: "Cinzel", serif;
    font-weight: 400;
    font-size: 22px;
    line-height: 1;
    padding: 2px 7px 1px;
  }
  .title {
    position: absolute;
    left: 262px;
    top: 68px;
    width: 560px;
    margin: 0;
    color: var(--gold);
    font-family: "Cinzel", serif;
    font-weight: 800;
    font-size: 50px;
    line-height: 1;
    letter-spacing: 1px;
    text-align: center;
    white-space: nowrap;
  }
  .subtitle {
    position: absolute;
    left: 262px;
    top: 124px;
    width: 560px;
    margin: 0;
    color: var(--white);
    font-family: "Cinzel", serif;
    font-weight: 700;
    font-size: 27px;
    line-height: 1;
    letter-spacing: 2.5px;
    text-align: center;
    white-space: nowrap;
  }
  .builder-label {
    position: absolute;
    left: 28px;
    top: 183px;
    color: var(--white);
    font-family: "Cinzel", serif;
    font-weight: 700;
    font-size: 14.5px;
    letter-spacing: 1.8px;
    line-height: 1;
  }
  .builder-name {
    position: absolute;
    left: 14px;
    top: 230px;
    width: 100px;
    text-align: center;
    color: var(--navy);
    font-family: "Cinzel", serif;
    font-weight: 700;
    font-size: 9.5px;
    line-height: 1.25;
  }
  .project-blurb {
    position: absolute;
    left: 122px;
    top: 216px;
    width: 310px;
    margin: 0;
    color: var(--navy-band);
    font-family: "Poppins", sans-serif;
    font-weight: 500;
    font-size: 9.6px;
    line-height: 1.25;
  }
  .agent-tag {
    position: absolute;
    left: 502px;
    top: 178px;
    display: flex;
    height: 25px;
    font-family: "Cinzel", serif;
    line-height: 25px;
    white-space: nowrap;
  }
  .agent-tag-label {
    background: var(--navy-band);
    color: var(--white);
    font-weight: 400;
    font-size: 14px;
    letter-spacing: 1.8px;
    padding: 0 9px;
  }
  .agent-tag-name {
    background: var(--gold);
    color: var(--navy-band);
    font-weight: 700;
    font-size: 14.5px;
    letter-spacing: 0.8px;
    padding: 0 16px 0 9px;
  }
  .agency {
    position: absolute;
    left: 502px;
    top: 210px;
    color: var(--gold);
    font-family: "Poppins", sans-serif;
    font-weight: 500;
    font-size: 10px;
    letter-spacing: 2.4px;
    line-height: 1;
  }
  .contact-line {
    position: absolute;
    left: 502px;
    display: flex;
    align-items: center;
    gap: 6px;
    color: var(--navy-band);
    font-family: "Poppins", sans-serif;
    font-weight: 600;
    font-size: 12.5px;
    line-height: 1;
  }
  .contact-phone { top: 227px; }
  .contact-email { top: 247px; }
  .contact-icon { width: 13px; height: 13px; }
  .agent-portrait {
    position: absolute;
    left: 842px;
    top: 32px;
    width: 124px;
    height: 258px;
    border-radius: 52px 52px 0 0;
    background: linear-gradient(180deg, #8c8c8c 0%, #5a5a5a 45%, #3f3f3f 100%);
  }
</style>
</head>
<body>
  <section class="banner">
    <svg class="banner-shapes" viewBox="0 0 985 290" width="985" height="290" aria-hidden="true">
      <defs>
        <linearGradient id="panelFade" x1="0" y1="0" x2="1" y2="1">
          <stop offset="0" stop-color="#ffffff"/>
          <stop offset="1" stop-color="#d9d9db"/>
        </linearGradient>
      </defs>
      <polygon points="452,176 985,176 985,290 500,290" fill="url(#panelFade)"/>
      <polygon points="700,176 985,176 985,290 860,290" fill="#e4e4e6" opacity="0.7"/>
      <polygon points="0,176 448,176 478,205 0,205" fill="#0b1738"/>
      <polyline points="0,176 448,176 478,205" fill="none" stroke="#e8b962" stroke-width="1.2"/>
      <polygon points="0,205 478,205 500,290 0,290" fill="#eabb66"/>
      <line x1="28" y1="258" x2="100" y2="258" stroke="#12245a" stroke-width="0.8"/>
    </svg>

    <div class="brand">
      <div class="brand-mark"></div>
      <div class="brand-name">FAIRLIGHT</div>
      <div class="brand-sub">REALTY</div>
    </div>

    <div class="launch">
      <span class="launch-script">Coming Spring</span>
      <span class="launch-year">2025</span>
    </div>
    <h1 class="title">THE ALDERMOOR</h1>
    <h2 class="subtitle">EXCLUSIVE LUXURY CONDOS</h2>

    <div class="builder-label">CONSTRUCTION BY STONEGATE BUILD GROUP</div>
    <div class="builder-name">STONEGATE BUILD GROUP</div>
    <p class="project-blurb">Unveil the height of luxury living with The Aldermoor, a new condo building in East Boston, set for completion in Spring 2025. Experience a standard of elegance and sophistication like never before.</p>

    <div class="agent-tag">
      <span class="agent-tag-label">LISTED BY</span>
      <span class="agent-tag-name">MARISOL QUENNELL</span>
    </div>
    <div class="agency">FAIRLIGHT REALTY</div>
    <div class="contact-line contact-phone">
      <svg class="contact-icon" viewBox="0 0 24 24" aria-hidden="true"><path fill="#0b1738" d="M6.6 10.8a15.1 15.1 0 0 0 6.6 6.6l2.2-2.2a1 1 0 0 1 1-.25 11.4 11.4 0 0 0 3.6.57 1 1 0 0 1 1 1V20a1 1 0 0 1-1 1A17 17 0 0 1 3 4a1 1 0 0 1 1-1h3.5a1 1 0 0 1 1 1c0 1.25.2 2.45.57 3.57a1 1 0 0 1-.25 1z"/></svg>
      <span>(617) 430-9162</span>
    </div>
    <div class="contact-line contact-email">
      <svg class="contact-icon" viewBox="0 0 24 24" aria-hidden="true"><path fill="#0b1738" d="M2 5h20v14H2z"/><path fill="none" stroke="#f3f3f4" stroke-width="1.6" d="M2.5 5.5 12 13l9.5-7.5"/></svg>
      <span>marisol@fairlightprops.com</span>
    </div>

    <div class="agent-portrait" role="img" aria-label="Black and white photo of the listing agent seated on a chair in a suit"></div>
  </section>
</body>
</html>
```